Association qui souhaite améliorer l'accès aux personnes en situation de handicap

Nous sommes une association qui a pour objectif d'améliorer l'accessibilité, augmenter l'offre des activités réalisables dans notre région touristique.
Nous souhaitons réaliser un site internet afin de pouvoir communiquer sur notre association. Nous avons déjà conçu notre flyer sur Plumotrix. Nous souhaiterions une base graphique se rapportant à celui-ci. C'est possible de tout retravailler mais nous souhaitons tout de même retrouver la charte graphique ou code couleur du flyer.
Il nous faudrait quelques pages:
- 1 page : Acceuil / Présentation (Home), Il y aurait le descriptif de l'association, avec ses objectifs à +/- moyen terme
- 1 page : Nos réalisations, celle-ci présenterait les éléments que nous avons réalisés avec des zones de textes et des images classées chronologiquement au fur et à mesure des nouveautés
- 1 page : Media, comme la précédente, mais ou on pourrait voir ou lire sur les divers médias qui parlent de nous
- 1 page : Evenements : c'est une page pour présenter divers activités que nous allons organiser
- 1 page : Contact qui indique comment nous contacter et avec la présentation des 5 ou 6 membres du comité
- 1 link donate : qui arrive sur un formulaire de donnée que l'on pourra faire évoluer sur un système de payement par la suite. Cette bannière doit se retrouver sur toutes les pages
Il est nécessaire que se design puisse être transféré sur une lecture sur téléphone mobile
Personnes en situation de handicap
Associatif

```html
<!DOCTYPE html>
<html lang="en">
<head>
<meta charset="utf-8">
<title>Open Paths Association</title>
<link href="https://fonts.googleapis.com/css2?family=Bebas+Neue&family=Montserrat:wght@400;500;600;700&display=swap" rel="stylesheet">
<style>
:root{
  --red:#c0171f;
  --dark:#1d2026;
  --ink:#1a1a1a;
  --text:#333;
  --muted:#555;
  --white:#fff;
  --cream:#fcfbf7;
  --line:#6b6b6b;
}
*{margin:0;padding:0;box-sizing:border-box}
html,body{width:1200px;height:3333px;overflow:hidden}
body{position:relative;background:var(--white);font-family:'Montserrat',sans-serif;color:var(--text)}
.abs{position:absolute}
.display{font-family:'Bebas Neue',sans-serif;letter-spacing:.5px}
.btn{position:absolute;background:var(--red);color:var(--white);border-radius:20px;font-size:11px;font-weight:600;display:flex;align-items:center;justify-content:center;text-transform:uppercase;letter-spacing:.3px}

/* top bar */
.topbar{top:0;left:0;width:1200px;height:28px;background:var(--red)}
.topbar .social{top:9px;width:10px;height:10px;border-radius:50%;background:var(--white)}
.topbar .phone{top:7px;right:129px;color:var(--white);font-size:11px;display:flex;align-items:center;gap:4px}

/* nav */
.nav{top:28px;left:0;width:1200px;height:61px;background:var(--white)}
.brand{display:flex;align-items:center;gap:8px;font-weight:700;font-size:13px;line-height:1.05;color:var(--ink);text-transform:uppercase}
.brand .mark{width:22px;height:22px;background:var(--red)}
.nav .brand{left:129px;top:13px}
.nav a{position:absolute;top:25px;font-size:11px;color:var(--ink);text-decoration:none}
.nav a.active{color:var(--red)}
.nav .donate{left:976px;top:16px;width:94px;height:30px;font-size:11px}

/* hero */
.hero{top:89px;left:0;width:1200px;height:443px}
.hero-copy{left:129px;top:126px;color:var(--white)}
.hero-copy .kicker{font-size:31px;line-height:1}
.hero-copy h1{font-size:45px;font-weight:700;line-height:1.1;margin-top:6px}
.hero-copy h1 span{color:var(--red)}
.hero-copy p{font-size:13px;line-height:19px;width:430px;margin-top:18px}
.hero .dot{top:409px;width:11px;height:11px;border-radius:50%;background:var(--white)}

/* welcome */
.photo-round{border-radius:34px}
.welcome-copy{left:610px;top:636px;width:460px}
.welcome-copy .kicker{font-size:21px;color:var(--ink)}
.welcome-copy h2{font-size:35px;font-weight:500;color:var(--ink);margin-top:2px}
.welcome-copy h2 span{color:var(--red)}
.body-copy{font-size:12.5px;line-height:19.4px;color:var(--text)}

/* achievements */
.achieve{top:1032px;left:0;width:1200px;height:515px}
.achieve-copy{left:132px;top:1158px;width:460px;color:var(--white)}
.achieve-copy h2{font-size:35px;font-weight:500}
.achieve-copy p{margin-top:26px;color:#eee}

/* media */
.section-title{width:1200px;left:0;text-align:center;font-weight:500;color:var(--ink)}
.media-card{top:1700px;width:300px;height:180px}
.media-caption{top:1860px;width:247px;height:40px;background:var(--white);box-shadow:0 2px 6px rgba(0,0,0,.12);font-size:12.5px;color:var(--ink);display:flex;align-items:center;justify-content:center;gap:6px}
.media-caption b{color:var(--red);font-size:15px}

/* events */
.events{top:1968px;left:0;width:1200px;height:568px}
.event-card{top:2096px;width:300px;height:370px;background:var(--white)}
.event-card .pic{position:absolute;left:0;top:0;width:300px;height:207px}
.event-card .date{position:absolute;left:15px;top:11px;width:36px;height:42px;background:var(--red);color:var(--white);font-size:9px;line-height:12px;text-align:center;padding-top:9px}
.event-card h3{position:absolute;left:22px;top:226px;font-size:16px;font-weight:500;color:var(--ink)}
.event-card p{position:absolute;left:24px;top:258px;width:255px;font-size:12.5px;line-height:19px;color:var(--muted)}
.event-card .btn{left:24px;top:312px;width:118px;height:39px}

/* contact */
.contact{top:2536px;left:0;width:1200px;height:400px;background:var(--cream)}
.contact-copy{left:608px;top:2645px}
.contact-copy h2{font-size:35px;font-weight:500;color:var(--ink)}
.contact-copy p{font-size:12.5px;color:var(--ink);margin-top:4px}
.field{border:1px solid var(--line);background:var(--white);font-size:10px;color:#555;padding:11px 10px}
.submit{background:var(--red);color:var(--white);font-size:10px;display:flex;align-items:center;justify-content:center;text-transform:uppercase}

/* footer */
.footer{left:0;top:2874px;width:1200px;height:459px}
.footer .brand{left:129px;top:3065px;color:var(--white);font-size:15px}
.footer .about{left:129px;top:3112px;width:210px;font-size:10.5px;line-height:16px;color:#ddd}
.footer .social{top:3176px;width:21px;height:21px;border-radius:50%;background:var(--red)}
.foot-col{top:3040px}
.foot-col h4{font-family:'Bebas Neue',sans-serif;font-size:19px;color:var(--red);font-weight:400;letter-spacing:.5px}
.foot-col ul{list-style:none;margin-top:4px}
.foot-col li{font-size:10.5px;color:var(--white);line-height:23px}
.contact-line{display:flex;align-items:center;gap:8px;font-size:10.5px;color:var(--white);height:22px;margin-top:21px}
.contact-line:first-of-type{margin-top:8px}
.contact-line .ico{width:22px;height:22px;border:1px solid var(--white);border-radius:50%;display:flex;align-items:center;justify-content:center}
.copyright{left:0;top:3269px;width:1200px;text-align:center;font-size:10px;color:var(--white)}
.copyright span{color:var(--red)}
</style>
</head>
<body>

<!-- Top bar -->
<div class="abs topbar">
  <span class="abs social" style="left:128px"></span>
  <span class="abs social" style="left:152px"></span>
  <div class="abs phone">
    <svg width="9" height="10" viewBox="0 0 24 24"><path fill="#fff" d="M6.6 10.8c1.4 2.8 3.8 5.1 6.6 6.6l2.2-2.2c.3-.3.7-.4 1-.2 1.1.4 2.3.6 3.6.6.6 0 1 .4 1 1V20c0 .6-.4 1-1 1C10.6 21 3 13.4 3 4c0-.6.4-1 1-1h3.5c.6 0 1 .4 1 1 0 1.3.2 2.5.6 3.6.1.3 0 .7-.2 1z"/></svg>
    +2 (555) 240 7316
  </div>
</div>

<!-- Navigation -->
<header class="abs nav">
  <div class="abs brand"><span class="mark"></span><span>Open Paths<br>Association</span></div>
  <a class="active" style="left:538px">Home</a>
  <svg class="abs" style="left:539px;top:42px" width="30" height="8" viewBox="0 0 30 8"><polyline points="1,2 6,6 11,2 16,6 21,2 26,6 29,3" fill="none" stroke="#c0171f" stroke-width="1.5"/></svg>
  <a style="left:610px">Our Achievements</a>
  <a style="left:742px">Media</a>
  <a style="left:813px">Events</a>
  <a style="left:887px">Contacts</a>
  <div class="btn donate">Donate</div>
</header>

<!-- Hero -->
<section class="abs hero">
  <svg class="abs" style="left:0;top:0" width="1200" height="443" role="img" aria-label="Photo of a young woman in a wheelchair beside a misty forest lake">
    <defs>
      <linearGradient id="heroBg" x1="0" y1="0" x2="1" y2="1">
        <stop offset="0" stop-color="#1f2a24"/>
        <stop offset=".55" stop-color="#3d4a44"/>
        <stop offset="1" stop-color="#8c9490"/>
      </linearGradient>
      <linearGradient id="heroShade" x1="0" y1="0" x2="1" y2="0">
        <stop offset="0" stop-color="#000" stop-opacity=".45"/>
        <stop offset=".6" stop-color="#000" stop-opacity="0"/>
      </linearGradient>
    </defs>
    <rect width="1200" height="443" fill="url(#heroBg)"/>
    <rect width="1200" height="443" fill="url(#heroShade)"/>
  </svg>
  <div class="abs hero-copy">
    <div class="kicker display">Access the</div>
    <h1>TOURIST <span>REGION</span></h1>
    <p>The resources of the association come from subscriptions, donations and events organized throughout the year.</p>
  </div>
  <div class="btn" style="left:129px;top:280px;width:118px;height:38px">Read more</div>
  <span class="abs dot" style="left:132px;background:var(--red)"></span>
  <span class="abs dot" style="left:153px"></span>
  <span class="abs dot" style="left:175px"></span>
</section>

<!-- Welcome -->
<svg class="abs photo-round" style="left:129px;top:599px" width="400" height="365" role="img" aria-label="Photo of a man with a white cane walking between garden columns">
  <defs><linearGradient id="welcomeImg" x1="0" y1="0" x2="1" y2="1"><stop offset="0" stop-color="#6f8f3a"/><stop offset=".5" stop-color="#c9c3a8"/><stop offset="1" stop-color="#3f4a2e"/></linearGradient></defs>
  <rect width="400" height="365" rx="34" fill="url(#welcomeImg)"/>
</svg>
<div class="abs welcome-copy">
  <div class="kicker display">Welcome to</div>
  <h2>Open <span>Paths</span> Association</h2>
  <p class="body-copy" style="margin-top:18px">Sed ut perspiciatis unde omnis iste natus error sit voluptatem accusantium doloremque laudantium, totam rem aperiam, eaque ipsa quae ab illo inventore veritatis et quasi architecto beatae vitae dicta sunt explicabo. Nemo enim ipsam voluptatem quia voluptas sit aspernatur aut odit aut fugit, sed quia consequuntur magni dolores eos qui ratione voluptatem sequi nesciunt.</p>
</div>
<div class="btn" style="left:610px;top:870px;width:118px;height:39px">Read more</div>

<!-- Achievements -->
<section class="abs achieve">
  <svg class="abs" style="left:0;top:0" width="1200" height="515" role="img" aria-label="Photos of a person in a wheelchair in a meadow and a hand touching tall grass">
    <defs>
      <linearGradient id="achLeft" x1="0" y1="0" x2="0" y2="1"><stop offset="0" stop-color="#2a2f2e"/><stop offset="1" stop-color="#2c3a26"/></linearGradient>
      <linearGradient id="achRight" x1="0" y1="0" x2="1" y2="1"><stop offset="0" stop-color="#7d8a5a"/><stop offset=".5" stop-color="#a7ac6a"/><stop offset="1" stop-color="#3a2a2c"/></linearGradient>
    </defs>
    <rect width="1200" height="515" fill="url(#achLeft)"/>
    <polygon points="729,0 1200,0 1200,515 1074,515 598,234" fill="url(#achRight)"/>
    <polyline points="729,0 598,234 1074,515" fill="none" stroke="#fff" stroke-width="6"/>
  </svg>
</section>
<div class="abs achieve-copy">
  <h2>Our Achievements</h2>
  <p class="body-copy">Sed ut perspiciatis unde omnis iste natus error sit voluptatem accusantium doloremque laudantium, totam rem aperiam, eaque ipsa quae ab illo inventore veritatis et quasi architecto beatae vitae dicta sunt explicabo. Nemo enim ipsam voluptatem quia voluptas sit aspernatur aut odit aut fugit, sed quia consequuntur magni dolores eos qui ratione voluptatem sequi nesciunt.</p>
</div>
<div class="btn" style="left:132px;top:1373px;width:117px;height:39px">Read more</div>

<!-- Media -->
<h2 class="abs section-title" style="top:1604px;font-size:35px">Our Media</h2>
<p class="abs section-title" style="top:1653px;font-size:12.5px;color:var(--text)">Sed ut perspiciatis unde omnis iste natus error sit voluptatem</p>

<svg class="abs media-card" style="left:129px" width="300" height="180" role="img" aria-label="Photo of a child helping an elderly woman in a wheelchair outdoors"><rect width="300" height="180" fill="#5f8a4a"/></svg>
<svg class="abs media-card" style="left:449px" width="300" height="180" role="img" aria-label="Photo of volunteers helping a person sitting in the snow"><rect width="300" height="180" fill="#c9ced2"/></svg>
<svg class="abs media-card" style="left:769px" width="300" height="180" role="img" aria-label="Photo of a doctor examining a seated patient"><rect width="300" height="180" fill="#b9b091"/></svg>

<div class="abs media-caption" style="left:157px">Voluptas Sit Aspernatur <b>+</b></div>
<div class="abs media-caption" style="left:477px">Voluptas Sit Aspernatur <b>+</b></div>
<div class="abs media-caption" style="left:797px">Voluptas Sit Aspernatur <b>+</b></div>

<!-- Events -->
<section class="abs events">
  <svg class="abs" style="left:0;top:0" width="1200" height="568" role="img" aria-label="Dark background photo of wheelchair users at an event"><rect width="1200" height="568" fill="#3a3d42"/></svg>
</section>
<h2 class="abs section-title" style="top:2030px;font-size:35px;color:var(--white)">Recent Event</h2>

<article class="abs event-card" style="left:129px">
  <svg class="pic" width="300" height="207" role="img" aria-label="Photo of a young girl blowing a dandelion on a lawn"><rect width="300" height="207" fill="#5aa23a"/></svg>
  <div class="date">12<br>MAY</div>
  <h3>Neque Porro Wuisquam</h3>
  <p>Sed ut perspiciatis unde omnis iste natus error sit voluptatem accusantium</p>
  <div class="btn">Read more</div>
</article>
<article class="abs event-card" style="left:449px">
  <svg class="pic" width="300" height="207" role="img" aria-label="Photo of people in wheelchairs gathered on a covered terrace"><rect width="300" height="207" fill="#7b8a78"/></svg>
  <div class="date">12<br>MAY</div>
  <h3>Neque Porro Wuisquam</h3>
  <p>Sed ut perspiciatis unde omnis iste natus error sit voluptatem accusantium</p>
  <div class="btn">Read more</div>
</article>
<article class="abs event-card" style="left:769px">
  <svg class="pic" width="300" height="207" role="img" aria-label="Photo of young wheelchair athletes racing on a court"><rect width="300" height="207" fill="#8a8f86"/></svg>
  <div class="date">12<br>MAY</div>
  <h3>Neque Porro Wuisquam</h3>
  <p>Sed ut perspiciatis unde omnis iste natus error sit voluptatem accusantium</p>
  <div class="btn">Read more</div>
</article>

<!-- Contact -->
<section class="abs contact"></section>

<!-- Footer background with slanted top -->
<svg class="abs footer" width="1200" height="459" aria-hidden="true">
  <polygon points="0,52 472,126 1200,0 1200,459 0,459" fill="#1d2026"/>
</svg>

<svg class="abs photo-round" style="left:129px;top:2603px" width="400" height="317" role="img" aria-label="Photo of a man riding an adapted hand bike on a grassy hillside">
  <defs><linearGradient id="contactImg" x1="0" y1="0" x2="1" y2="1"><stop offset="0" stop-color="#8aa36a"/><stop offset=".5" stop-color="#b8403e"/><stop offset="1" stop-color="#6d6f70"/></linearGradient></defs>
  <rect width="400" height="317" rx="34" fill="url(#contactImg)"/>
</svg>

<div class="abs contact-copy">
  <h2>Contact Us</h2>
  <p>Sed ut perspiciatis unde omnis iste natus error</p>
</div>
<div class="abs field" style="left:610px;top:2743px;width:227px;height:35px">Name:</div>
<div class="abs field" style="left:610px;top:2790px;width:227px;height:35px">Email:</div>
<div class="abs field" style="left:610px;top:2837px;width:227px;height:36px">Phone:</div>
<div class="abs field" style="left:843px;top:2743px;width:227px;height:82px">Comments:</div>
<div class="abs submit" style="left:843px;top:2837px;width:227px;height:36px">Submit</div>

<!-- Footer content -->
<div class="abs brand" style="left:129px;top:3065px;color:var(--white);font-size:15px"><span class="mark"></span><span>Open Paths<br>Association</span></div>
<p class="abs about" style="left:129px;top:3112px;width:210px;font-size:10.5px;line-height:16px;color:#ddd">Sed ut perspiciatis unde omnis iste natus error sit voluptatem accusantium rem aperiam</p>
<span class="abs" style="left:130px;top:3176px;width:21px;height:21px;border-radius:50%;background:var(--red)"></span>
<span class="abs" style="left:165px;top:3176px;width:21px;height:21px;border-radius:50%;background:var(--red)"></span>

<div class="abs foot-col" style="left:449px">
  <h4>Sitemap</h4>
  <ul><li>Home</li><li>Our Achivements</li><li>Media</li><li>Events</li><li>Contact Us</li></ul>
</div>
<div class="abs foot-col" style="left:669px">
  <h4>Others</h4>
  <ul><li>Privacy Policy</li><li>Terms &amp; Conditions</li><li>Leagal</li><li>Donate</li><li>Help / Support</li></ul>
</div>
<div class="abs foot-col" style="left:875px">
  <h4>Contacts</h4>
  <div class="contact-line"><span class="ico"><svg width="10" height="12" viewBox="0 0 24 24"><path fill="#c0171f" d="M12 2a7 7 0 0 0-7 7c0 5 7 13 7 13s7-8 7-13a7 7 0 0 0-7-7zm0 9.5A2.5 2.5 0 1 1 12 6.5a2.5 2.5 0 0 1 0 5z"/></svg></span>Larch Road 40 Val Montane</div>
  <div class="contact-line"><span class="ico"><svg width="10" height="10" viewBox="0 0 24 24"><path fill="#c0171f" d="M6.6 10.8c1.4 2.8 3.8 5.1 6.6 6.6l2.2-2.2c.3-.3.7-.4 1-.2 1.1.4 2.3.6 3.6.6.6 0 1 .4 1 1V20c0 .6-.4 1-1 1C10.6 21 3 13.4 3 4c0-.6.4-1 1-1h3.5c.6 0 1 .4 1 1 0 1.3.2 2.5.6 3.6.1.3 0 .7-.2 1z"/></svg></span>+2 (555) 240 7316</div>
  <div class="contact-line"><span class="ico"><svg width="11" height="9" viewBox="0 0 24 18"><rect x="1" y="1" width="22" height="16" rx="2" fill="#c0171f"/><polyline points="2,2 12,10 22,2" fill="none" stroke="#1d2026" stroke-width="2"/></svg></span>info@openpathsassociation.org</div>
</div>

<p class="abs copyright">Copyright © 2022 <span>Open Paths Association</span>. All Rights Reserved.</p>

</body>
</html>
```